Tolbek cards

I want a simple business card that pops.
Logo on one side.
On side two i want.
"Are you thinking about a new building on your property, or renovating an existing structure? Contact".....
Owners Name: Dale Whitacre
Owners Phone number: 610-555-0187
Address:4076 Copper Ridge RD, Millbrook, OH 43215
Committed to Quality, Service, and Integrity

```html
<!DOCTYPE html>
<html lang="en">
<head>
<meta charset="UTF-8">
<title>Tolbek Builders — Business Cards</title>
<link href="https://fonts.googleapis.com/css2?family=Michroma&family=Montserrat:wght@700;800&family=Lato:wght@400;700&display=swap" rel="stylesheet">
<style>
  :root {
    --stage: #2f2f30;
    --brown: #3f2c1c;
    --cream: #fbe0c0;
    --white: #ffffff;
    --logo-brown: #3b2816;
    --deco-dark: #5e3f24;
    --deco-light: #b09a84;
  }
  html, body {
    margin: 0;
    width: 1200px;
    height: 689px;
    overflow: hidden;
    background: var(--stage);
  }
  .stage {
    position: relative;
    width: 1200px;
    height: 689px;
    display: flex;
    align-items: center;
    justify-content: center;
    gap: 48px;
  }
  .card {
    position: relative;
    width: 540px;
    height: 309px;
    border-radius: 22px;
    overflow: hidden;
    box-shadow: 0 18px 40px rgba(0,0,0,.45);
  }

  /* Contact side */
  .card--back {
    background: var(--brown);
    color: var(--cream);
  }
  .card--back .pitch {
    position: absolute;
    left: 34px;
    top: 30px;
    margin: 0;
    font-family: "Michroma", sans-serif;
    font-size: 12.5px;
    line-height: 1.5;
    text-transform: uppercase;
    letter-spacing: .02em;
    white-space: nowrap;
    z-index: 1;
  }
  .card--back .owner-name {
    position: absolute;
    left: 34px;
    top: 146px;
    margin: 0;
    font-family: "Montserrat", sans-serif;
    font-weight: 800;
    font-size: 24px;
    line-height: 1;
    letter-spacing: .03em;
    text-transform: uppercase;
    z-index: 1;
  }
  .card--back .owner-role {
    position: absolute;
    left: 34px;
    top: 176px;
    margin: 0;
    font-family: "Lato", sans-serif;
    font-size: 13px;
  }
  .card--back .address {
    position: absolute;
    left: 34px;
    top: 204px;
    margin: 0;
    font-family: "Lato", sans-serif;
    font-style: normal;
    font-size: 13px;
    line-height: 1.4;
  }
  .card--back .address strong { font-weight: 700; }
  .card--back .phone {
    position: absolute;
    left: 34px;
    top: 264px;
    display: flex;
    align-items: center;
    gap: 6px;
    font-family: "Lato", sans-serif;
    font-weight: 700;
    font-size: 17px;
  }
  .card--back .phone svg { width: 13px; height: 13px; }
  .card--back .brand-art {
    position: absolute;
    right: 0;
    top: 0;
    width: 200px;
    height: 309px;
    background: linear-gradient(135deg, var(--cream) 0%, #e9c9a4 100%);
    clip-path: polygon(30% 0, 100% 0, 100% 100%, 0 100%, 20% 50%);
  }

  /* Logo side */
  .card--front { background: var(--white); }
  .card--front .brand-art {
    position: absolute;
    left: 0;
    bottom: 0;
    width: 290px;
    height: 210px;
    background: linear-gradient(120deg, var(--deco-dark) 0%, var(--deco-light) 100%);
    clip-path: polygon(0 20%, 45% 0, 100% 100%, 0 100%);
  }
  .card--front .wordmark {
    position: absolute;
    right: 34px;
    top: 96px;
    display: flex;
    align-items: center;
    gap: 14px;
    font-family: "Montserrat", sans-serif;
    font-weight: 800;
    color: var(--logo-brown);
  }
  .card--front .wordmark-square {
    width: 22px;
    height: 22px;
    background: var(--logo-brown);
  }
  .card--front .wordmark-text {
    display: flex;
    flex-direction: column;
    align-items: center;
    line-height: 1;
  }
  .card--front .wordmark-name {
    font-size: 56px;
    letter-spacing: .01em;
  }
  .card--front .wordmark-sub {
    margin-top: 6px;
    font-size: 18px;
    letter-spacing: .12em;
  }
</style>
</head>
<body>
<main class="stage">
  <section class="card card--back" aria-label="Business card, contact side">
    <p class="pitch">Are you thinking<br>about a new building<br>on your property, or<br>renovating an existing<br>structure? Contact.....</p>
    <h1 class="owner-name">Dale Whitacre</h1>
    <p class="owner-role">Owner</p>
    <address class="address">
      <strong>Tolbek Builders LLC</strong><br>
      4076 Copper Ridge RD<br>
      Millbrook, OH 43215
    </address>
    <div class="phone">
      <svg viewBox="0 0 24 24" aria-hidden="true"><path fill="currentColor" d="M6.6 10.8a15.1 15.1 0 0 0 6.6 6.6l2.2-2.2c.3-.3.7-.4 1-.2 1.1.4 2.3.6 3.6.6.6 0 1 .4 1 1V20c0 .6-.4 1-1 1A17 17 0 0 1 3 4c0-.6.4-1 1-1h3.5c.6 0 1 .4 1 1 0 1.3.2 2.5.6 3.6.1.3 0 .7-.2 1z"/></svg>
      <span>610-555-0187</span>
    </div>
    <div class="brand-art" role="img" aria-label="Large decorative brand graphic in cream"></div>
  </section>

  <section class="card card--front" aria-label="Business card, logo side">
    <div class="brand-art" role="img" aria-label="Large decorative brand graphic in brown gradient"></div>
    <div class="wordmark">
      <span class="wordmark-square" aria-hidden="true"></span>
      <div class="wordmark-text">
        <span class="wordmark-name">TOLBEK</span>
        <span class="wordmark-sub">BUILDERS LLC</span>
      </div>
    </div>
  </section>
</main>
</body>
</html>
```